Kesso Tea Premium Matcha brand Label

This is a label design project for a luxury tea brand. Feel free to be creative within the guidelines.
Attached to this project is a document called “Private Label Design Requirements” with the design guidelines and template. There is another document called "Kesso Tea Packaging Instructions" this has more details necessary to stick to the guidelines in the first document.

I have also attached the certifications to be included as well as different variations of the logo for you to use.

If you have any questions, I am here.
Updates

Need extra days to review

Target Market(s)

Young, active, fun, enjoy the finer things

```html
<!DOCTYPE html>
<html lang="en">
<head>
<meta charset="utf-8">
<title>Kesso Tea – Premium Organic Ceremonial Matcha Label</title>
<link rel="stylesheet" href="https://fonts.googleapis.com/css2?family=Oswald:wght@400;500&family=Questrial&display=swap">
<style>
  :root {
    --backdrop: #e4f0d6;
    --paper: #f7f9f4;
    --leaf-tint: #e3eedb;
    --band-dark: #232323;
    --matcha: #7fd12b;
    --text-light: #ffffff;
    --text-dark: #1e1e1e;
    --badge-grey: #ececec;
  }
  * { margin: 0; padding: 0; box-sizing: border-box; }
  html, body {
    width: 1200px; height: 800px; overflow: hidden;
    background: var(--backdrop);
    font-family: "Questrial", "Century Gothic", sans-serif;
  }
  .canvas { position: relative; width: 1200px; height: 800px; }

  .label {
    position: absolute; left: 72px; top: 312px;
    width: 1056px; height: 176px;
    background: var(--band-dark);
    box-shadow: 0 6px 18px rgba(0,0,0,0.12);
  }
  .label__pattern {
    position: absolute; left: 0; top: 0; width: 100%; height: 66px;
    background: linear-gradient(90deg, var(--paper), var(--leaf-tint) 50%, var(--paper));
  }

  .refrigerate-tag {
    position: absolute; left: 49px; top: 18px;
    width: 207px; height: 27px;
    border: 1.5px solid var(--text-dark); border-radius: 6px;
    background: var(--paper);
    font-family: "Oswald", "Arial Narrow", sans-serif;
    font-weight: 500; font-size: 12px; letter-spacing: 0.5px;
    color: var(--text-dark); white-space: nowrap;
    display: flex; align-items: center; justify-content: center;
  }

  .brand-mark {
    position: absolute; left: 502px; top: 14px;
    width: 52px; height: 52px; border-radius: 50%;
    background: var(--band-dark); border: 2px solid var(--paper);
    display: flex; align-items: center; justify-content: center;
    font-size: 9px; color: var(--text-light); white-space: nowrap;
  }

  .distributor {
    position: absolute; left: 50px; top: 72px;
    font-size: 12px; line-height: 13px; color: var(--text-light);
    white-space: nowrap;
  }
  .heading-green {
    color: var(--matcha); font-style: italic; font-size: 12.5px;
    white-space: nowrap;
  }
  .badges { position: absolute; left: 218px; top: 121px; display: flex; gap: 28px; align-items: center; }
  .badge-square { width: 34px; height: 33px; background: var(--badge-grey); }
  .badge-round { width: 30px; height: 30px; border-radius: 50%; background: var(--text-light); }

  .product-title {
    position: absolute; left: 0; right: 0; top: 80px;
    text-align: center; font-family: "Oswald", "Arial Narrow", sans-serif;
    white-space: nowrap;
  }
  .product-title__line1 { font-size: 24px; line-height: 26px; font-weight: 400; color: var(--text-light); letter-spacing: 0.6px; }
  .product-title__line2 { font-size: 35px; line-height: 34px; font-weight: 500; color: var(--matcha); letter-spacing: 1px; }
  .net-weight { font-family: "Questrial", sans-serif; font-size: 17px; line-height: 20px; color: var(--text-light); }

  .ingredients { position: absolute; left: 786px; top: 26px; }
  .ingredients__list { font-size: 12.5px; color: var(--text-dark); margin-top: 2px; white-space: nowrap; }

  .brew-guide { position: absolute; left: 786px; top: 74px; }
  .brew-guide__steps { list-style: none; margin-top: 4px; color: var(--text-light); font-size: 12.5px; line-height: 15.5px; white-space: nowrap; }
  .brew-guide__steps li { position: relative; padding-left: 15px; }
  .brew-guide__steps li::before {
    content: ""; position: absolute; left: 1px; top: 4px;
    width: 7px; height: 7px; background: var(--matcha);
    border-radius: 0 60% 0 60%;
  }
</style>
</head>
<body>
<main class="canvas">
  <section class="label" aria-label="Matcha tin wrap label">
    <div class="label__pattern" role="img" aria-label="Soft repeating leaf pattern band"></div>

    <div class="refrigerate-tag">KEEP REFRIGERATED FOR QUALITY</div>

    <div class="brand-mark">Kesso Tea</div>

    <div class="distributor">
      <div class="heading-green">Distributed by:</div>
      <div>Kesso Tea Co.</div>
      <div>412 Linden Ave NE Suite B-204</div>
      <div>Greenvale Ga 30499</div>
      <div>Certified Organic by vrda</div>
      <div>PRODUCT OF JAPAN</div>
    </div>
    <div class="badges">
      <div class="badge-square" role="img" aria-label="Non-GMO certification badge"></div>
      <div class="badge-round" role="img" aria-label="Organic certification seal"></div>
    </div>

    <div class="product-title">
      <div class="product-title__line1">PREMIUM ORGANIC</div>
      <div class="product-title__line2">CEREMONIAL MATCHA</div>
      <div class="net-weight">Net Wt: 30g (1.06oz)</div>
    </div>

    <div class="ingredients">
      <div class="heading-green">Ingredients:</div>
      <div class="ingredients__list">Organic Matcha Green Tea</div>
    </div>

    <div class="brew-guide">
      <div class="heading-green">For The Perfect Cup Of Matcha:</div>
      <ul class="brew-guide__steps">
        <li>1-2 grams of Matcha</li>
        <li>2oz of Water (170-180 degrees F)</li>
        <li>Whisk in a W formation until frothy</li>
        <li>Sweeten to taste</li>
      </ul>
    </div>
  </section>
</main>
</body>
</html>
```